BRAMBLEFORD CONSTRUCTIONS B-Card

I currently have a b-card design but will be removing the image (tree) from the logo and have text only.
I want the card to be classy and strong within the building and construction industry.
I will be using Spot UV on the cards as per the attached examples. I will also send through some sketched ideas that I have in mind.
The color blue is similar to the image (No. 6) attached images

Target Market(s)

middle to maturre aged.
Home Owners / Renovators and Builders

Industry/Entity Type

Construction

Contact Information for Business Card

BRAMBLEFORD CONSTRUCTIONS
Name: Gareth Pennick
Title: Project Manager
Mobile: 0427 351 804
Office: (08) 9316 5172
Address: 47C Corvell Street, Tennby KR 5120
Email: info@bramblefordhomes.com.au
PO Box: 3817 Tennby KR 5177

Colors
0592cd
33a6d7
85cae6
1b1b1b

Requirements
Must have
• 1. It must have spot UV on the front of card, maybe back of card too
• 2. I really like the blue on image 6. (or at least a really cool electric blue against the charcoal grey background)
• 3. The font must be slimline and modern. Easy to read
• 4. There must be no black used on the card... Only greys and dark charcoal greys
• 5. Use only the text from the logo "Brambleford Constructions" Not the image of the tree. I am wanting the b-cards to be more masculine.
Nice to have
• 1. I like the design concept on image 6. but happy to see what else you can do with the Spot UV
• 2. Unless you have a really cool idea of the image of the tree (from previous logo) Spot UV somewhere in the design concept thats original and different then I am keen to see what you come up with
• 3. Try changing the color of the logo eg. full white or Blue and white
• 4. Another option is to have the Brambleford Logo on the front of card with the spot UV in the background of text which we specialise in eg, Roofing, Ceiling, Insulation, Gutter Guards, Electrical, Insurance etc and we can add or reduce items as required. Similar to image 12.
Should not have
• Do not include the image of the tree from previous logo. unless you have a really cool idea of Spot UV somewhere in the design concept thats original and different.

```html
<!DOCTYPE html>
<html lang="en">
<head>
<meta charset="utf-8">
<title>Brambleford Constructions – Business Card</title>
<link rel="stylesheet" href="https://fonts.googleapis.com/css2?family=Jost:wght@400;500&display=swap">
<style>
  :root {
    --stage: #3a3a3a;
    --card: #1b1b1b;
    --card-edge: #262626;
    --blue: #0592cd;
    --blue-bright: #33a6d7;
    --text: #e4e4e4;
    --text-muted: #c8c8c8;
    --divider: #8a8a8a;
  }
  * { box-sizing: border-box; margin: 0; padding: 0; }
  html, body {
    width: 1200px; height: 747px; overflow: hidden;
    background: var(--stage);
    font-family: "Jost", sans-serif;
  }
  .stage {
    position: relative; width: 1200px; height: 747px;
    display: flex; align-items: center; justify-content: center; gap: 40px;
  }
  .card {
    width: 540px; height: 330px;
    background: var(--card);
    border: 1px solid var(--card-edge);
    border-radius: 16px;
    position: relative;
    color: var(--text);
  }
  .brand-name {
    color: var(--text);
    font-weight: 500;
    letter-spacing: 0;
    line-height: 1.15;
  }

  /* Logo side */
  .card--logo {
    display: flex; flex-direction: column; align-items: center; justify-content: center;
  }
  .card--logo .brand-name { font-size: 30px; text-align: center; }
  .services {
    margin-top: 26px; text-align: center;
    font-size: 15px; color: var(--text-muted); letter-spacing: 0.5px; line-height: 1.45;
  }
  .services .sep { margin: 0 6px; }

  /* Contact side */
  .card--contact { display: flex; align-items: center; }
  .card--contact .brand-block { width: 270px; padding-left: 34px; padding-right: 20px; }
  .card--contact .brand-name { font-size: 22px; }
  .divider {
    position: absolute; left: 282px; top: 26px; bottom: 78px;
    width: 1px; background: linear-gradient(var(--card), var(--divider) 30%, var(--divider) 70%, var(--card));
  }
  .contact {
    position: absolute; left: 300px; top: 34px; right: 16px;
    font-size: 14px; line-height: 1.3; color: var(--text);
  }
  .person { color: var(--blue-bright); font-size: 22px; font-weight: 500; line-height: 1.1; }
  .role { font-size: 16px; margin-bottom: 10px; }
  .address { margin-bottom: 10px; }
  .line { display: flex; align-items: center; gap: 10px; }
  .line svg { width: 14px; height: 14px; flex: none; fill: var(--blue-bright); }
</style>
</head>
<body>
<main class="stage">

  <section class="card card--logo">
    <p class="brand-name">Brambleford Constructions</p>
    <p class="services">
      Roofing<span class="sep">|</span>Ceiling<span class="sep">|</span>Insulation<span class="sep">|</span>Gutter Guards<br>
      Electrical<span class="sep">|</span>Insurance etc
    </p>
  </section>

  <section class="card card--contact">
    <div class="brand-block">
      <p class="brand-name">Brambleford Constructions</p>
    </div>
    <div class="divider"></div>
    <div class="contact">
      <p class="person">Gareth Pennick</p>
      <p class="role">Project Manager</p>
      <p class="address">47C Corvell Street<br>Tennby KR 5120</p>
      <p class="address">PO Box: 3817 Tennby<br>KR 5177</p>
      <p class="line">
        <svg viewBox="0 0 24 24" aria-hidden="true"><path d="M6.6 10.8a15.1 15.1 0 0 0 6.6 6.6l2.2-2.2a1 1 0 0 1 1-.25 11.4 11.4 0 0 0 3.6.57 1 1 0 0 1 1 1V20a1 1 0 0 1-1 1A17 17 0 0 1 3 4a1 1 0 0 1 1-1h3.5a1 1 0 0 1 1 1c0 1.25.2 2.45.57 3.6a1 1 0 0 1-.25 1z"/></svg>
        (08) 9316 5172
      </p>
      <p class="line">
        <svg viewBox="0 0 24 24" aria-hidden="true"><path d="M7 1h10a2 2 0 0 1 2 2v18a2 2 0 0 1-2 2H7a2 2 0 0 1-2-2V3a2 2 0 0 1 2-2zm0 3v14h10V4zm5 15.5a1 1 0 1 0 0 2 1 1 0 0 0 0-2z"/></svg>
        0427 351 804
      </p>
      <p class="line">
        <svg viewBox="0 0 24 24" aria-hidden="true"><path d="M2 5h20v14H2zm2 2v.4l8 5.1 8-5.1V7zm0 2.8V17h16V9.8l-8 5.1z"/></svg>
        info@bramblefordhomes.com.au
      </p>
    </div>
  </section>

</main>
</body>
</html>
```